Velmora Consulting Business

** Please add the content information from my old business card
1. I would like to see a two sided business card with both options with the 1st Option--Tallow Spire-new WHITE BACKGROUND LOGO
2 nd Option-Tallow Spire - new BLACK- Background Logo
3rd -Option a business card with my Photo on the card
Please add the new word to the card information:
EXECUTION
AS THE OWNER'S REP
WE AIM TO ACHIEVE YOUR
INFRASTRUCTURE VISION with
OUR SPECIALIZATION & EXECUTION in:

FUNDING Planning
BUSINESS Planning
INFRASTRUCTURE Planning
PROJECT Management
Since 2012
_____________________________________________________________________
I want to get spot uv raised printing. I was liking a a nice rich white linen paper stock with black writing & NOT A COLORED CARD other than a variety of white or black cards concept

```html
<!DOCTYPE html>
<html lang="en">
<head>
<meta charset="utf-8">
<title>Velmora Consulting – Business Cards</title>
<link href="https://fonts.googleapis.com/css2?family=Open+Sans:wght@400;600;700&display=swap" rel="stylesheet">
<style>
  :root {
    --stage: #2e2e2e;
    --card-black: #231f20;
    --card-white: #f3f3f1;
    --ink-light: #ffffff;
    --ink-dark: #231f20;
    --accent-red: #e4173e;
    --rule-grey: #8a8a8a;
  }
  * { box-sizing: border-box; margin: 0; padding: 0; }
  html, body { width: 1200px; height: 689px; overflow: hidden; }
  body {
    background: var(--stage);
    font-family: "Open Sans", Arial, sans-serif;
    position: relative;
  }
  .card {
    position: absolute;
    top: 190px;
    width: 530px;
    height: 303px;
    border-radius: 18px;
    overflow: hidden;
  }
  .card--back { left: 45px; background: var(--card-black); color: var(--ink-light); }
  .card--front { left: 625px; background: var(--card-white); color: var(--ink-dark); }

  .brand {
    position: absolute;
    left: 40px;
    top: 110px;
    width: 200px;
    display: flex;
    flex-direction: column;
    align-items: flex-start;
  }
  .brand__row { display: flex; align-items: center; gap: 8px; }
  .brand__square { width: 12px; height: 12px; background: var(--accent-red); }
  .brand__name { font-size: 40px; font-weight: 700; line-height: 1; letter-spacing: -0.5px; }
  .brand__tag {
    margin-top: 6px;
    font-size: 11px;
    font-weight: 700;
    letter-spacing: 9px;
    line-height: 1;
  }

  .divider {
    position: absolute;
    left: 262px;
    top: 70px;
    width: 1px;
    height: 170px;
  }
  .card--back .divider { background: linear-gradient(to bottom, transparent, #9a9a9a, transparent); }
  .card--front .divider { background: linear-gradient(to bottom, transparent, var(--rule-grey), transparent); }

  .pitch {
    position: absolute;
    left: 290px;
    top: 52px;
    width: 225px;
    font-size: 10.5px;
    line-height: 1.35;
  }
  .pitch__statement { margin-bottom: 14px; }
  .services { list-style: none; }
  .services li { display: flex; align-items: center; gap: 8px; }
  .services__mark { width: 6px; height: 6px; background: var(--accent-red); flex: none; }
  .pitch__since { margin-top: 6px; padding-left: 14px; }

  .contact {
    position: absolute;
    left: 290px;
    top: 62px;
    width: 225px;
  }
  .contact__name { font-size: 15px; font-weight: 700; line-height: 1.2; }
  .contact__role { font-size: 10px; margin-bottom: 14px; }
  .contact__list { list-style: none; font-size: 11px; line-height: 1.75; }
  .contact__list li { display: flex; align-items: center; gap: 9px; }
  .contact__list svg { width: 11px; height: 11px; fill: var(--ink-dark); flex: none; }
  .contact__cities { margin-top: 10px; font-size: 11px; }
  .contact__dot { color: var(--accent-red); font-weight: 700; }

  .front-band {
    position: absolute;
    left: 0; right: 0; bottom: 0;
    height: 22px;
    background: var(--card-black);
    border-top: 2px solid var(--card-white);
    box-shadow: 0 -3px 0 var(--accent-red);
  }
</style>
</head>
<body>

<section class="card card--back" aria-label="Business card, black side">
  <div class="brand">
    <div class="brand__row">
      <span class="brand__name">Velmora</span>
      <span class="brand__square"></span>
    </div>
    <span class="brand__tag">CONSULTING</span>
  </div>

  <div class="divider"></div>

  <div class="pitch">
    <p class="pitch__statement">
      EXECUTION<br>
      AS THE OWNER'S REP<br>
      WE AIM TO ACHIEVE YOUR<br>
      INFRASTRUCTURE VISION with<br>
      OUR SPECIALIZATION &amp; EXECUTION in:
    </p>
    <ul class="services">
      <li><span class="services__mark"></span>FUNDING Planning</li>
      <li><span class="services__mark"></span>BUSINESS Planning</li>
      <li><span class="services__mark"></span>INFRASTRUCTURE Planning</li>
      <li><span class="services__mark"></span>PROJECT Management</li>
    </ul>
    <p class="pitch__since">Since 2012</p>
  </div>
</section>

<section class="card card--front" aria-label="Business card, white side">
  <div class="brand">
    <div class="brand__row">
      <span class="brand__name">Velmora</span>
      <span class="brand__square"></span>
    </div>
    <span class="brand__tag">CONSULTING</span>
  </div>

  <div class="divider"></div>

  <div class="contact">
    <p class="contact__name">Marisol Keene-Oduya</p>
    <p class="contact__role">CEO / LEAD PROJECT MANAGER</p>
    <ul class="contact__list">
      <li>
        <svg viewBox="0 0 24 24" aria-hidden="true"><path d="M6.6 10.8a15.1 15.1 0 0 0 6.6 6.6l2.2-2.2a1 1 0 0 1 1-.25 11.4 11.4 0 0 0 3.6.57 1 1 0 0 1 1 1V20a1 1 0 0 1-1 1A17 17 0 0 1 3 4a1 1 0 0 1 1-1h3.5a1 1 0 0 1 1 1c0 1.25.2 2.45.57 3.57a1 1 0 0 1-.25 1z"/></svg>
        555 010.0182
      </li>
      <li>
        <svg viewBox="0 0 24 24" aria-hidden="true"><path d="M2 5h20v14H2z M3.5 6.5 12 13l8.5-6.5" fill="none" stroke="#231f20" stroke-width="2"/></svg>
        mar@velmora.ca
      </li>
      <li>
        <svg viewBox="0 0 24 24" aria-hidden="true"><circle cx="12" cy="12" r="9" fill="none" stroke="#231f20" stroke-width="2"/><path d="M3 12h18M12 3c3 3 3 15 0 18M12 3c-3 3-3 15 0 18" fill="none" stroke="#231f20" stroke-width="1.6"/></svg>
        www.velmora.ca
      </li>
    </ul>
    <p class="contact__cities">Larkmoor NT <span class="contact__dot">•</span> Brennfield NB</p>
  </div>

  <div class="front-band"></div>
</section>

</body>
</html>
```